Gobal construction supply company needs new business card design

I need a business card design for my global supply company using an existing logo. i will be looking to print these on rounded corner cards with the black background version of my logo on the back. on the front white background, my logo again and my simple details.

```html
<!DOCTYPE html>
<html lang="en">
<head>
<meta charset="utf-8">
<title>Meridian Supply Works – Business Card</title>
<link href="https://fonts.googleapis.com/css2?family=Lato:wght@400;700&display=swap" rel="stylesheet">
<style>
  :root {
    --page-bg: #e9e7e4;
    --card-black: #0b0b0b;
    --card-white: #f7f7f7;
    --ink: #2b2b2b;
    --ink-soft: #555555;
    --brand-red: #e0171f;
    --white: #ffffff;
  }
  * { margin: 0; padding: 0; box-sizing: border-box; }
  html, body {
    width: 1200px; height: 886px; overflow: hidden;
    background: var(--page-bg);
    font-family: "Lato", sans-serif;
  }
  .canvas { position: relative; width: 1200px; height: 886px; }
  .card {
    position: absolute; left: 260px;
    width: 680px; height: 388px;
    border-radius: 26px;
    box-shadow: 0 10px 24px rgba(0,0,0,0.18);
  }
  .card-back { top: 38px; background: var(--card-black); }
  .card-front { top: 460px; background: var(--card-white); }

  .brand {
    display: flex; align-items: center; gap: 10px;
    font-weight: 700; letter-spacing: 0.06em;
    text-transform: uppercase; white-space: nowrap;
  }
  .brand-dot {
    width: 14px; height: 14px; border-radius: 50%;
    background: var(--brand-red); flex: none;
  }
  .card-back .brand {
    position: absolute; left: 50%; top: 50%;
    transform: translate(-50%, -50%);
    color: var(--white); font-size: 30px; gap: 12px;
  }
  .card-back .brand-dot { width: 16px; height: 16px; }
  .card-front .brand {
    position: absolute; left: 40px; top: 140px;
    color: var(--ink); font-size: 18px;
  }

  .contact {
    position: absolute; left: 372px; top: 118px;
    list-style: none;
  }
  .contact li {
    display: flex; align-items: center; gap: 14px;
    color: var(--ink-soft); font-size: 16px; margin-bottom: 12px;
  }
  .contact .person { margin-bottom: 22px; }
  .icon {
    width: 26px; height: 26px; flex: none;
    background: var(--brand-red); border-radius: 3px;
    box-shadow: 0 2px 3px rgba(0,0,0,0.25);
    display: flex; align-items: center; justify-content: center;
  }
  .person .icon { width: 34px; height: 34px; }
  .person-name {
    color: var(--ink); font-size: 24px; letter-spacing: 0.04em;
    text-transform: uppercase; line-height: 1.05;
  }
  .person-title {
    color: var(--brand-red); font-size: 17px;
    text-transform: uppercase; letter-spacing: 0.02em;
  }
</style>
</head>
<body>
<main class="canvas">
  <section class="card card-back" aria-label="Card back">
    <div class="brand"><span class="brand-dot"></span>Meridian Supply Works</div>
  </section>

  <section class="card card-front" aria-label="Card front">
    <div class="brand"><span class="brand-dot"></span>Meridian Supply Works</div>

    <ul class="contact">
      <li class="person">
        <span class="icon">
          <svg width="18" height="18" viewBox="0 0 18 18"><circle cx="9" cy="6" r="3.5" fill="#fff"/><path d="M2 17c0-4 3-6 7-6s7 2 7 6z" fill="#fff"/></svg>
        </span>
        <div>
          <div class="person-name">Daniel Reyes</div>
          <div class="person-title">CEO/Founder</div>
        </div>
      </li>
      <li>
        <span class="icon">
          <svg width="14" height="16" viewBox="0 0 14 16"><rect x="2.5" y="0.5" width="9" height="15" rx="1.5" fill="none" stroke="#fff" stroke-width="1.5"/><circle cx="7" cy="12.5" r="1" fill="#fff"/></svg>
        </span>
        555 -014 -2938
      </li>
      <li>
        <span class="icon">
          <svg width="16" height="12" viewBox="0 0 16 12"><rect x="0.75" y="0.75" width="14.5" height="10.5" fill="none" stroke="#fff" stroke-width="1.5"/><path d="M1 1l7 6 7-6" fill="none" stroke="#fff" stroke-width="1.5"/></svg>
        </span>
        daniel@meridiansupply.com
      </li>
      <li>
        <span class="icon">
          <svg width="16" height="16" viewBox="0 0 16 16"><circle cx="8" cy="8" r="6.5" fill="none" stroke="#fff" stroke-width="1.5"/><ellipse cx="8" cy="8" rx="3" ry="6.5" fill="none" stroke="#fff" stroke-width="1.2"/><path d="M1.5 8h13" stroke="#fff" stroke-width="1.2"/></svg>
        </span>
        www.meridiansupply.com
      </li>
    </ul>
  </section>
</main>
</body>
</html>
```